VIP Card Design Project

uZorvo is a premium sneaker store selling brand name sneakers like Volta, Rexa, Kembro and etc. ( www.uzorvoshop.com ) We need to design a VIP card to promote one of our discount program called "Uzorvo VIP Band 17", which offers 24% discount off all full-priced items. The idea is because we have a "Peakline Gym center" (peaklinegym.com) next door and we are trying to design a discount program for people going to the fitness center.
The design is for the front of the card. The back will be black and white with benefits information and member information.
The front design need to include our logo, "VIP", "Band 17" and our web address "Uzorvo.com" and Chatterly and quibbr logo.
It will be a plastic card in the size of 3.375x2.125 (bleed size 3.5x2.25)

```html
<!DOCTYPE html>
<html lang="en">
<head>
<meta charset="utf-8">
<title>Uzorvo VIP Band 17 – Card</title>
<link href="https://fonts.googleapis.com/css2?family=Luckiest+Guy&family=Arimo:wght@400;700&display=swap" rel="stylesheet">
<style>
  :root{
    --stage:#ece9e5;
    --card:#ffffff;
    --card-tint:#f5edf1;
    --green:#3fae3c;
    --orange:#f07a1a;
    --red:#d4141e;
    --ink:#2a1a14;
    --yellow:#f7ea1c;
    --body-text:#555555;
    --chatterly:#3b5aa0;
    --quibbr:#37b6e6;
  }
  *{box-sizing:border-box;margin:0;padding:0}
  html,body{width:1200px;height:665px;overflow:hidden}
  body{background:var(--stage);position:relative;font-family:"Arimo",Arial,sans-serif}

  .card{
    position:absolute;top:168px;width:520px;height:328px;
    border-radius:6px;overflow:hidden;
    background:linear-gradient(135deg,var(--card) 0%,var(--card) 40%,var(--card-tint) 100%);
    box-shadow:0 4px 14px rgba(0,0,0,.18);
  }
  .card--front{left:50px}
  .card--back{left:630px}

  /* Front */
  .brand-logo{
    position:absolute;left:38px;top:36px;
    font-family:"Luckiest Guy","Arial Black",sans-serif;font-size:88px;line-height:1;
    color:var(--green);letter-spacing:1px;
  }
  .brand-url{
    position:absolute;left:142px;top:134px;
    font-weight:700;font-size:16px;color:var(--orange);letter-spacing:1px;
  }
  .social{position:absolute;right:18px;top:18px;display:flex;flex-direction:column;gap:12px;align-items:center}
  .social__item{display:flex;flex-direction:column;align-items:center;gap:2px;font-size:10px;font-weight:700}
  .social__mark{width:30px;height:30px;border-radius:5px}
  .social__item--quibbr{color:var(--quibbr)}
  .social__item--quibbr .social__mark{background:var(--quibbr)}
  .social__item--chatterly{color:var(--chatterly)}
  .social__item--chatterly .social__mark{background:var(--chatterly)}

  .club-title{
    position:absolute;left:44px;top:186px;white-space:nowrap;
    font-family:"Luckiest Guy","Arial Black",sans-serif;font-size:36px;line-height:1;
    color:var(--red);-webkit-text-stroke:1px var(--ink);
    transform:rotate(-7deg);transform-origin:left bottom;
  }
  .photo{position:absolute;border-radius:3px}
  .photo--runner{left:60px;top:246px;width:122px;height:70px;background:linear-gradient(135deg,#6a5a4e,#c8473a 55%,#3a3030)}
  .photo--court{left:200px;top:226px;width:138px;height:72px;background:linear-gradient(135deg,#d8a02a,#e04a2a 45%,#3a62b0)}
  .photo--classic{left:372px;top:200px;width:116px;height:68px;background:linear-gradient(135deg,#b88a3a,#f2efe9 45%,#d33a2a)}

  .offer-band{position:absolute;left:0;top:0;width:520px;height:328px}
  .offer-text{font-family:"Arimo",Arial,sans-serif;font-weight:700;font-size:12.5px;letter-spacing:1px;fill:var(--ink)}
  .offer-burst-text{font-family:"Luckiest Guy","Arial Black",sans-serif;font-size:18px;fill:var(--red)}

  /* Back */
  .benefits{position:absolute;inset:0;padding:30px 30px 0 30px;color:var(--body-text);font-size:11.5px;line-height:1.4}
  .benefits__title{text-align:center;font-weight:700;font-size:15px;color:var(--ink);margin-bottom:8px}
  .benefits__title span{color:var(--green)}
  .benefits__intro{margin-bottom:10px}
  .benefits__list{list-style:none;padding-left:14px}
  .benefits__list li{display:flex;gap:6px;margin-bottom:9px}
  .benefits__letter{color:var(--green);min-width:12px}
  .member{position:absolute;left:30px;right:24px;bottom:22px;display:flex;gap:16px;color:var(--orange);font-size:12px}
  .member__field{flex:1;display:flex;align-items:flex-end;gap:6px;white-space:nowrap}
  .member__line{flex:1;border-bottom:1px solid #bbb;height:12px}
</style>
</head>
<body>

<section class="card card--front" aria-label="Card front">
  <div class="brand-logo">uZorvo</div>
  <div class="brand-url">www.Uzorvo.com</div>

  <div class="social">
    <div class="social__item social__item--quibbr"><span class="social__mark"></span>quibbr</div>
    <div class="social__item social__item--chatterly"><span class="social__mark"></span>Chatterly</div>
  </div>

  <div class="club-title">Uzorvo VIP Band 17</div>

  <div class="photo photo--runner" role="img" aria-label="Photo of red and grey Volta running sneakers"></div>
  <div class="photo photo--court" role="img" aria-label="Photo of white, blue and orange Arcwing basketball sneaker"></div>
  <div class="photo photo--classic" role="img" aria-label="Photo of white and red Stridel basketball sneaker"></div>

  <svg class="offer-band" viewBox="0 0 520 328">
    <g transform="rotate(-6 330 292)">
      <rect x="160" y="282" width="350" height="22" rx="9" fill="var(--yellow)" stroke="var(--ink)" stroke-width="1.5"/>
      <text class="offer-text" x="180" y="298">DISCOUNT OFF ALL FULL-PRICED ITEMS.</text>
    </g>
    <polygon fill="var(--yellow)" stroke="var(--ink)" stroke-width="1.2"
      points="50,262 58,276 73,268 71,284 89,284 77,296 91,306 73,310 77,324 61,316 51,328 45,314 29,320 33,306 15,302 29,292 17,280 35,282 33,266 45,276"/>
    <text class="offer-burst-text" x="31" y="303">24%</text>
  </svg>
</section>

<section class="card card--back" aria-label="Card back">
  <div class="benefits">
    <h2 class="benefits__title">-: <span>Benefits</span> :-</h2>
    <p class="benefits__intro">The UZORVO Member Program entitles Members to the following benefits:</p>
    <ol class="benefits__list">
      <li><span class="benefits__letter">a.</span><span>20% OFF your entire first purchase after you sign up (Limited Time Offer). Certain items are excluded from this offer. Please see stores for details.</span></li>
      <li><span class="benefits__letter">b.</span><span>10% OFF every purchase while being a member. Certain items are excluded from this offer. Please see stores for details.</span></li>
      <li><span class="benefits__letter">c.</span><span>Additional 10% OFF and FREE SHIPPING when an item is out of stock in store but can be shipped to you from another location.</span></li>
      <li><span class="benefits__letter">d.</span><span>Eligible to purchase exclusive items offered to members only. Purchasing of exclusive items is limited to 1 item per member per 30 days. Please see stores for details.</span></li>
    </ol>
  </div>
  <div class="member">
    <div class="member__field">Member Name :<span class="member__line"></span></div>
    <div class="member__field">Member ID :<span class="member__line"></span></div>
  </div>
</section>

</body>
</html>
```